Walk Beside The River

Business Card design

Target Market(s)

People who require support in the commnity

Industry/Entity Type

Mental Health Support

Contact Information for Business Card

Mental Health Support Rosalind Tavener walkbesidetheriver@mailcove.com.au 0481 637 092 PO Box 926 Kellerton QLD 4571

Colors
6B429C
8869AF
B7A5CE
E3DAEB
F3F0F8

Requirements
Must have
• Logo & details listed above
Should not have
• No red or orange

```html
<!DOCTYPE html>
<html lang="en">
<head>
<meta charset="utf-8">
<title>Walk Beside The River — Business Card</title>
<link rel="stylesheet" href="https://fonts.googleapis.com/css2?family=Open+Sans:wght@400;600&display=swap">
<style>
  :root {
    --page: #0e0e10;
    --card: #232228;
    --brand-purple: #6b429c;
    --text-light: #f3f0f8;
    --accent-yellow: #f2e93a;
  }
  * { margin: 0; padding: 0; box-sizing: border-box; }
  html, body { width: 1200px; height: 780px; overflow: hidden; }
  body {
    background: var(--page);
    font-family: "Open Sans", Arial, sans-serif;
    position: relative;
  }
  .card {
    position: absolute;
    top: 235px;
    width: 540px;
    height: 310px;
    background: var(--card);
    border-radius: 2px;
    overflow: hidden;
  }
  .card--front { left: 40px; }
  .card--back { left: 620px; }

  .brand {
    position: absolute;
    display: flex;
    align-items: center;
    gap: 14px;
  }
  .brand__disc {
    width: 96px;
    height: 96px;
    border-radius: 50%;
    background: var(--brand-purple);
    flex: none;
  }
  .brand__name {
    color: var(--text-light);
    font-weight: 600;
    font-size: 16px;
    letter-spacing: 0.18em;
    text-transform: uppercase;
    line-height: 1.4;
    width: 170px;
  }
  .card--front .brand { left: 34px; top: 28px; }
  .card--back .brand { right: 40px; top: 40px; }

  .details {
    position: absolute;
    left: 34px;
    bottom: 28px;
    color: var(--text-light);
    font-size: 16px;
    line-height: 1.45;
    list-style: none;
  }
  .details li { display: flex; align-items: center; gap: 10px; white-space: nowrap; }
  .details .with-icon { padding-left: 20px; }
  .details svg { width: 18px; height: 18px; flex: none; }
</style>
</head>
<body>

  <section class="card card--front" aria-label="Business card front">
    <div class="brand">
      <span class="brand__disc"></span>
      <span class="brand__name">Walk Beside The River</span>
    </div>
    <ul class="details">
      <li>Mental Health Support</li>
      <li>Rosalind Tavener</li>
      <li class="with-icon">
        <svg viewBox="0 0 24 24" aria-hidden="true"><path fill="var(--accent-yellow)" d="M6.6 10.8a15.1 15.1 0 0 0 6.6 6.6l2.2-2.2c.3-.3.7-.4 1-.2 1.1.4 2.3.6 3.6.6.6 0 1 .4 1 1V20c0 .6-.4 1-1 1A17 17 0 0 1 3 4c0-.6.4-1 1-1h3.5c.6 0 1 .4 1 1 0 1.3.2 2.5.6 3.6.1.3 0 .7-.2 1z"/></svg>
        0481 637 092
      </li>
      <li class="with-icon">
        <svg viewBox="0 0 24 24" aria-hidden="true"><rect x="2.5" y="5" width="19" height="14" rx="1.5" fill="none" stroke="var(--accent-yellow)" stroke-width="2"/><path d="M3 6l9 7 9-7" fill="none" stroke="var(--accent-yellow)" stroke-width="2"/></svg>
        walkbesidetheriver@mailcove.com.au
      </li>
      <li class="with-icon">
        <svg viewBox="0 0 24 24" aria-hidden="true"><path fill="var(--accent-yellow)" d="M12 2a7 7 0 0 0-7 7c0 5.2 7 13 7 13s7-7.8 7-13a7 7 0 0 0-7-7zm0 9.5A2.5 2.5 0 1 1 12 6.5a2.5 2.5 0 0 1 0 5z"/></svg>
        PO Box 926 Kellerton QLD 4571
      </li>
    </ul>
  </section>

  <section class="card card--back" aria-label="Business card back">
    <div class="brand">
      <span class="brand__disc"></span>
      <span class="brand__name">Walk Beside The River</span>
    </div>
  </section>

</body>
</html>
```